BOLD & MINIMALIST DESIGN NEEDED

We want a very bold but minimalistic business card design that is impactful and utilizes both sides of the business card. Our current logo is included for your use.

We want bold fonts and good use of negative space. We don't want the logo to overpower the design.

Target Market(s)

Professionals who are building new commercial buildings.

Industry/Entity Type

Construction

Contact Information for Business Card

Name, Title, email, office phone, cell phone, website

Font styles to use
Serif
Sans Serif

Requirements
Must have
• Bold design!

```html
<!DOCTYPE html>
<html lang="en">
<head>
<meta charset="utf-8">
<title>Ridgeline Build Co – Business Card</title>
<link rel="stylesheet" href="https://fonts.googleapis.com/css2?family=Archivo+Black&family=Montserrat:wght@600;700;800&family=Michroma&display=swap">
<style>
  :root {
    --page: #ffffff;
    --card-front: #0c0d0f;
    --card-back: #000000;
    --green: #96cb4a;
    --white: #ffffff;
    --arc: #1a1b1e;
  }
  html, body {
    margin: 0;
    padding: 0;
    width: 1200px;
    height: 1200px;
    overflow: hidden;
    background: var(--page);
  }
  .canvas {
    position: relative;
    width: 1200px;
    height: 1200px;
  }
  .card {
    position: absolute;
    left: 228px;
    width: 751px;
    height: 429px;
    border-radius: 18px;
    overflow: hidden;
  }
  .card--front { top: 149px; background: var(--card-front); }
  .card--back  { top: 642px; background: var(--card-back); }

  .front-arc {
    position: absolute;
    left: 0; top: 0;
    width: 751px; height: 429px;
  }
  .front-brand {
    position: absolute;
    left: 72px;
    top: 338px;
    display: flex;
    align-items: center;
    gap: 10px;
  }
  .brand-square {
    width: 18px; height: 18px;
    background: var(--green);
  }
  .brand-name {
    font-family: "Archivo Black", sans-serif;
    color: var(--white);
    font-size: 24px;
    letter-spacing: 0.5px;
    line-height: 1;
  }

  .website {
    position: absolute;
    left: 76px; top: 70px;
    font-family: "Montserrat", sans-serif;
    font-weight: 800;
    font-size: 22px;
    color: var(--white);
    letter-spacing: 0.3px;
  }
  .icon-dot {
    position: absolute;
    width: 30px; height: 30px;
    border-radius: 50%;
    background: var(--green);
    display: flex;
    align-items: center;
    justify-content: center;
  }
  .contact {
    position: absolute;
    font-family: "Montserrat", sans-serif;
    font-weight: 700;
    color: var(--white);
    font-size: 18px;
    line-height: 23px;
  }
  .phone-dot { left: 488px; top: 70px; }
  .phone { left: 530px; top: 73px; font-size: 19px; }
  .email-dot { left: 311px; top: 242px; }
  .email { left: 351px; top: 244px; font-size: 17px; }
  .pin-dot { left: 81px; top: 337px; }
  .address { left: 125px; top: 333px; }

  .name {
    position: absolute;
    left: 76px; top: 110px;
    width: 592px; height: 124px;
  }
  .name text {
    font-family: "Archivo Black", sans-serif;
    fill: var(--green);
  }
  .title {
    position: absolute;
    left: 76px; top: 244px;
    font-family: "Michroma", sans-serif;
    font-size: 22px;
    letter-spacing: 9px;
    color: var(--white);
    line-height: 1;
  }
  .back-brand {
    position: absolute;
    right: 77px; top: 330px;
    font-family: "Archivo Black", sans-serif;
    color: var(--white);
    font-size: 17px;
    line-height: 1;
  }
</style>
</head>
<body>
<div class="canvas">

  <section class="card card--front">
    <svg class="front-arc" viewBox="0 0 751 429" aria-hidden="true">
      <path d="M170 429 C 330 360, 560 340, 751 404" fill="none" stroke="var(--arc)" stroke-width="3"/>
    </svg>
    <div class="front-brand">
      <span class="brand-square"></span>
      <span class="brand-name">RIDGELINE BUILD CO</span>
    </div>
  </section>

  <section class="card card--back">
    <div class="website">www.r-b-c.com</div>

    <div class="icon-dot phone-dot">
      <svg width="16" height="16" viewBox="0 0 24 24" fill="none" stroke="#000" stroke-width="1.8" stroke-linecap="round" stroke-linejoin="round" aria-hidden="true">
        <path d="M22 16.9v3a2 2 0 0 1-2.2 2 19.8 19.8 0 0 1-8.6-3.1 19.5 19.5 0 0 1-6-6A19.8 19.8 0 0 1 2.1 4.2 2 2 0 0 1 4.1 2h3a2 2 0 0 1 2 1.7c.1 1 .4 1.9.7 2.8a2 2 0 0 1-.5 2.1L8 9.9a16 16 0 0 0 6 6l1.3-1.3a2 2 0 0 1 2.1-.5c.9.3 1.8.6 2.8.7a2 2 0 0 1 1.7 2z"/>
      </svg>
    </div>
    <div class="contact phone">555.014.2290</div>

    <svg class="name" viewBox="0 0 592 124" role="img" aria-label="Jonah">
      <text x="0" y="122" font-size="170" textLength="592" lengthAdjust="spacingAndGlyphs">JONAH</text>
    </svg>

    <div class="title">OWNER</div>

    <div class="icon-dot email-dot">
      <svg width="16" height="16" viewBox="0 0 24 24" fill="none" stroke="#000" stroke-width="1.8" stroke-linejoin="round" aria-hidden="true">
        <rect x="3" y="5" width="18" height="14" rx="1"/>
        <path d="M3 6l9 7 9-7M3 18l6-6M21 18l-6-6"/>
      </svg>
    </div>
    <div class="contact email">jonah@ridgelinebuildco.com</div>

    <div class="icon-dot pin-dot">
      <svg width="16" height="18" viewBox="0 0 24 24" fill="none" stroke="#000" stroke-width="1.8" aria-hidden="true">
        <path d="M12 22s7-7.2 7-12.5A7 7 0 0 0 5 9.5C5 14.8 12 22 12 22z"/>
        <circle cx="12" cy="9.5" r="2.5"/>
      </svg>
    </div>
    <div class="contact address">18 Stone Mill Rd., Harlow, GA,<br>United States, 30599</div>

    <div class="back-brand">RIDGELINE BUILD CO</div>
  </section>

</div>
</body>
</html>
```